Develop website for Cloud Security Startup

Looking for a logo that conveys the outsourced security and management of clients data, systems and development in Tellix, Bri and Pindle with an emphasis on security and compliance

Target Market(s)

Companies looking for professional services IT firm

Coding

Coded - Design and coding required

Number of Pages Required

5+ page

Font styles to use
Sans Serif

Colors
0455a3
33a6d7

Requirements
Must have
• Landing Page
- Help me get started

Move to the cloud safely
- Benefits of Cloud

What we do
- Cloud Adoption
- Managed Services
- Optimise

Resources
- News
- Resources
- Events
- Webinars
- Not for profit
- Case Studies
- Support Button
- Incident Button

Company
- About Us
- Why Vorplexa?
- Acreditations
- Quorvane Tellix Partner
- Net Promoter Score
- Careers
- Contact Us

Contact Us

```html
<!DOCTYPE html>
<html lang="en">
<head>
<meta charset="utf-8">
<title>Vorplexa — Cloud Security</title>
<link href="https://fonts.googleapis.com/css2?family=Lato:wght@300;400;700;900&display=swap" rel="stylesheet">
<style>
:root{
  --navy:#0a3d8a;
  --brand:#0455a3;
  --sky:#33a6d7;
  --deep:#0b2a66;
  --ink:#333a45;
  --muted:#555c66;
  --grey:#efefef;
  --white:#ffffff;
}
*{margin:0;padding:0;box-sizing:border-box}
html,body{width:1200px;height:4736px;overflow:hidden}
body{position:relative;font-family:'Lato',sans-serif;color:var(--ink);background:var(--white)}
.abs{position:absolute}
a{text-decoration:none;color:inherit}

/* header */
.site-header{position:absolute;top:0;left:0;width:1200px;height:151px;background:var(--white)}
.brand{position:absolute;left:74px;top:36px;display:flex;flex-direction:column;align-items:flex-start}
.brand-mark{width:40px;height:40px;border-radius:50%;background:var(--brand);margin-left:48px;margin-bottom:10px}
.brand-name{font-weight:900;font-size:30px;letter-spacing:1px;color:var(--brand);line-height:1}
.main-nav{position:absolute;top:72px;left:301px}
.main-nav a{position:absolute;font-weight:900;font-size:14px;color:#1b1f27;white-space:nowrap}
.btn-pill{position:absolute;display:flex;align-items:center;justify-content:center;border-radius:28px;color:var(--white);font-weight:900;font-size:15px;letter-spacing:.3px}
.btn-support{left:814px;top:55px;width:151px;height:53px;background:var(--brand)}
.btn-incident{left:974px;top:55px;width:151px;height:53px;background:var(--sky)}

/* hero */
.hero{position:absolute;top:151px;left:0;width:1200px;height:768px}
.hero svg.bg{position:absolute;inset:0}
.hero-title{position:absolute;left:74px;top:199px;font-size:68px;font-weight:900;color:var(--white);letter-spacing:1px;line-height:80px}
.hero-sub{position:absolute;left:74px;top:288px;width:460px;font-size:24px;font-weight:700;line-height:37px;color:var(--white)}
.btn-read{position:absolute;width:189px;height:48px;border-radius:26px;background:linear-gradient(90deg,var(--brand),var(--sky));color:var(--white);font-weight:900;font-size:16px;display:flex;align-items:center;justify-content:center}
.hero-art{position:absolute;left:542px;top:100px;width:634px;height:460px;border-radius:20px;background:radial-gradient(ellipse at center,rgba(51,166,215,.55),rgba(11,42,102,0) 70%)}
.divider-mark{position:absolute;left:568px;top:906px;width:50px;height:50px;border-radius:50%;background:var(--brand);border:6px solid var(--sky)}

/* section headings */
.eyebrow{font-size:29px;font-weight:400;color:var(--sky)}
.heading{font-size:44px;font-weight:900;color:var(--brand);line-height:48px}
.centered{position:absolute;left:0;width:1200px;text-align:center}
.lede{font-size:16px;color:var(--ink)}
.body-copy{font-size:15.5px;line-height:33px;color:var(--ink)}

/* benefits */
.feature{position:absolute;width:300px}
.feature-icon{position:absolute;left:0;top:0;width:42px;height:42px;border-radius:50%;background:var(--brand);border:5px solid var(--sky)}
.feature h4{margin-left:62px;font-size:16px;font-weight:900;color:var(--brand)}
.feature p{margin-left:62px;margin-top:10px;font-size:14px;line-height:26px;color:var(--ink);width:230px}

/* service cards */
.card{position:absolute;background:var(--white);border-radius:8px;box-shadow:0 6px 20px rgba(0,0,0,.08);text-align:center}
.service{top:1871px;width:331px;height:316px;padding-top:40px}
.service h3{margin-top:28px;font-size:21px;font-weight:900;color:var(--brand)}
.service p{margin:10px auto 0;width:270px;font-size:15px;line-height:28px;color:var(--ink)}
.service.featured{background:linear-gradient(160deg,var(--brand),#1a76c4);overflow:hidden}
.service.featured h3,.service.featured p{position:relative;color:var(--white)}
.service.featured .glow{position:absolute;left:150px;top:110px;width:160px;height:160px;border-radius:50%;background:rgba(255,255,255,.1)}
.service svg{display:block;margin:0 auto;position:relative}

/* company */
.company-art{position:absolute;left:643px;top:2325px;width:484px;height:463px;border-radius:50% 50% 50% 50%/45% 45% 55% 55%;background:radial-gradient(circle at 40% 45%,#e8f6fc 0,#8fd0ee 30%,#33a6d7 55%,#0455a3 85%)}

/* resources */
.resource{top:3180px;width:331px;height:507px;text-align:left;overflow:hidden}
.resource .thumb{height:228px;width:100%}
.resource .meta{padding:28px 25px 0}
.resource .cat{font-size:14px;font-weight:900;color:var(--brand)}
.resource h3{margin-top:10px;font-size:23px;line-height:33px;font-weight:700;color:var(--brand)}
.resource p{margin-top:10px;font-size:15.5px;line-height:28px;color:var(--ink)}
.resource .more{display:block;margin-top:18px;font-size:14px;font-weight:900;color:var(--brand)}
.dots{position:absolute;top:3754px;left:553px;display:flex;gap:14px}
.dots span{width:12px;height:12px;border-radius:50%;background:#333}
.dots span:first-child{background:var(--sky)}

/* clients */
.clients{position:absolute;top:4090px;left:0;width:1200px;display:flex;justify-content:center;gap:100px}
.client-name{font-size:56px;font-weight:700;color:var(--brand);line-height:60px}

/* footer */
.site-footer{position:absolute;top:4268px;left:0;width:1200px;height:468px;background:linear-gradient(90deg,var(--navy),var(--brand) 50%,#2a8fd0);color:var(--white);overflow:hidden}
.footer-glow{position:absolute;left:720px;top:180px;width:420px;height:420px;border-radius:50%;background:rgba(255,255,255,.06)}
.footer-brand{position:absolute;left:74px;top:60px}
.footer-brand .brand-mark{background:var(--white);width:56px;height:56px;margin-left:62px;margin-bottom:14px}
.footer-brand .brand-name{color:var(--white);font-size:38px}
.footer-about{position:absolute;left:74px;top:208px;width:270px;font-size:14px;line-height:27px}
.footer-col{position:absolute;top:64px}
.footer-col h5{font-size:18px;font-weight:900;margin-bottom:12px}
.footer-col li{list-style:none;font-size:14px;line-height:34px}
.footer-rule{position:absolute;left:0;top:382px;width:1200px;height:1px;background:rgba(255,255,255,.25)}
.copyright{position:absolute;left:74px;top:414px;font-size:13px}
.social{position:absolute;right:60px;top:412px;display:flex;gap:16px}
.social span{width:18px;height:18px;border-radius:50%;background:var(--white)}
</style>
</head>
<body>

<header class="site-header">
  <div class="brand">
    <span class="brand-mark"></span>
    <span class="brand-name">VORPLEXA</span>
  </div>
  <nav class="main-nav">
    <a href="#" style="left:0">WHAT WE DO</a>
    <a href="#" style="left:153px">COMPANY</a>
    <a href="#" style="left:280px">RESOURCES</a>
    <a href="#" style="left:419px">CONTACT</a>
  </nav>
  <a href="#" class="btn-pill btn-support">SUPPORT</a>
  <a href="#" class="btn-pill btn-incident">INCIDENT</a>
</header>

<section class="hero">
  <svg class="bg" width="1200" height="768" viewBox="0 0 1200 768">
    <defs>
      <linearGradient id="heroGrad" x1="0" y1="0" x2="1" y2="1">
        <stop offset="0" stop-color="#0d3a7e"/>
        <stop offset=".6" stop-color="#0b2f6e"/>
        <stop offset="1" stop-color="#0a2a63"/>
      </linearGradient>
    </defs>
    <polygon points="0,0 1200,0 1200,630 600,768 0,630" fill="url(#heroGrad)"/>
  </svg>
  <div class="hero-art" role="img" aria-label="Isometric illustration of a padlocked cloud connected to laptops, screens and people"></div>
  <h1 class="hero-title">VORPLEXA</h1>
  <p class="hero-sub">We are a cloud security startup outsourcing security and management of clients data.</p>
  <a href="#" class="btn-read" style="left:74px;top:428px">READ MORE</a>
</section>
<span class="divider-mark"></span>

<section class="benefits">
  <p class="eyebrow abs" style="left:74px;top:1030px">Move to the cloud safely</p>
  <h2 class="heading abs" style="left:74px;top:1075px">BENEFITS OF<br>CLOUD</h2>
  <p class="body-copy abs" style="left:74px;top:1180px;width:410px">Sed ut perspiciatis unde omnis iste natus error sit voluptatem accusantium doloremque laudantium, totam rem aperiam, eaque ipsa quae ab illo inventore veritatis et quasi architecto beatae.</p>
  <a href="#" class="btn-read" style="left:74px;top:1340px">READ MORE</a>

  <div class="feature" style="left:524px;top:1058px"><span class="feature-icon"></span><h4>SED UT PERSPICIATIS</h4><p>Sed ut perspiciatis unde omnis iste natus error sit voluptatem accusantium laudantium otam rem aperiam.</p></div>
  <div class="feature" style="left:857px;top:1058px"><span class="feature-icon"></span><h4>SED UT PERSPICIATIS</h4><p>Sed ut perspiciatis unde omnis iste natus error sit voluptatem accusantium laudantium otam rem aperiam.</p></div>
  <div class="feature" style="left:524px;top:1234px"><span class="feature-icon"></span><h4>SED UT PERSPICIATIS</h4><p>Sed ut perspiciatis unde omnis iste natus error sit voluptatem accusantium laudantium otam rem aperiam.</p></div>
  <div class="feature" style="left:857px;top:1234px"><span class="feature-icon"></span><h4>SED UT PERSPICIATIS</h4><p>Sed ut perspiciatis unde omnis iste natus error sit voluptatem accusantium laudantium otam rem aperiam.</p></div>
</section>

<svg class="abs" style="left:0;top:1448px" width="1200" height="790" viewBox="0 0 1200 790" aria-hidden="true">
  <polygon points="0,0 600,150 1200,0 1200,628 600,787 0,628" fill="var(--grey)"/>
</svg>

<section class="services">
  <p class="eyebrow centered" style="top:1678px">Our Services</p>
  <h2 class="heading centered" style="top:1722px">WHAT WE DO</h2>
  <p class="lede centered" style="top:1786px">Sed ut perspiciatis unde omnis iste natus error sit&nbsp; voluptatem accusantium doloremque laudantium, totam rem aperiam.</p>

  <article class="card service" style="left:74px">
    <svg width="90" height="60" viewBox="0 0 90 60"><path d="M20 56h52a16 16 0 0 0 0-32 24 24 0 0 0-46-4A18 18 0 0 0 20 56z" fill="var(--brand)"/></svg>
    <h3>CLOUD ADOPTION</h3>
    <p>Sed ut perspiciatis unde omnis iste natus error sit&nbsp; voluptatem accusantium doloremque laudantiumtotam.</p>
  </article>
  <article class="card service featured" style="left:436px">
    <span class="glow"></span>
    <svg width="70" height="70" viewBox="0 0 70 70" fill="none" stroke="#fff" stroke-width="9"><path d="M12 32a23 23 0 0 1 42-12"/><path d="M58 38a23 23 0 0 1-42 12"/><path d="M56 6v16H40" stroke-width="8"/><path d="M14 64V48h16" stroke-width="8"/></svg>
    <h3>MANAGED SERVICES</h3>
    <p>Sed ut perspiciatis unde omnis iste natus error sit&nbsp; voluptatem accusantium doloremque laudantiumtotam.</p>
  </article>
  <article class="card service" style="left:796px">
    <svg width="90" height="70" viewBox="0 0 90 70" fill="var(--brand)"><circle cx="32" cy="40" r="20"/><circle cx="32" cy="40" r="7" fill="#fff"/><circle cx="66" cy="20" r="12"/><circle cx="66" cy="20" r="4" fill="#fff"/><circle cx="68" cy="54" r="10"/><circle cx="68" cy="54" r="3.5" fill="#fff"/></svg>
    <h3>OPTIMISE</h3>
    <p>Sed ut perspiciatis unde omnis iste natus error sit&nbsp; voluptatem accusantium doloremque laudantiumtotam.</p>
  </article>
</section>

<section class="company">
  <p class="eyebrow abs" style="left:74px;top:2393px">Who We Are</p>
  <h2 class="heading abs" style="left:74px;top:2437px">OUR COMPANY</h2>
  <p class="body-copy abs" style="left:74px;top:2497px;width:480px">Sed ut perspiciatis unde omnis iste natus error sit voluptatem accusantium doloremque laudantium, totam rem aperiam, eaque ipsa quae ab illo inventore veritatis et quasi architecto beatae.</p>
  <a href="#" class="btn-read" style="left:74px;top:2661px">READ MORE</a>
  <div class="company-art" role="img" aria-label="Circular ring of digital service icons around a central security keyhole"></div>
</section>

<svg class="abs" style="left:0;top:2775px" width="1200" height="1120" viewBox="0 0 1200 1120" aria-hidden="true">
  <polygon points="0,0 600,160 1200,0 1200,956 600,1118 0,956" fill="var(--grey)"/>
</svg>

<section class="resources">
  <p class="eyebrow centered" style="top:3004px">What's New</p>
  <h2 class="heading centered" style="top:3049px">RESOURCES</h2>
  <p class="lede centered" style="top:3113px">Sed ut perspiciatis unde omnis iste natus error sit&nbsp; voluptatem accusantium doloremque laudantium, totam rem aperiam.</p>

  <article class="card resource" style="left:74px">
    <div class="thumb" role="img" aria-label="Photo of a glowing laptop with cloud network graphics" style="background:linear-gradient(135deg,#0b2a66,#1a6fc0 55%,#33a6d7)"></div>
    <div class="meta"><span class="cat">NEWS</span><h3>Sed ut perspiciatis unde omnis iste</h3><p>Nemo enim ipsam voluptatem quia voluptas sit aspernatur aut odit aut fugit, sed quia consequuntur.</p><a href="#" class="more">READ MORE</a></div>
  </article>
  <article class="card resource" style="left:434px">
    <div class="thumb" role="img" aria-label="Photo of hands typing with a digital padlock overlay" style="background:linear-gradient(135deg,#4a4f57,#8a9098 55%,#2f343b)"></div>
    <div class="meta"><span class="cat">RESOURCES</span><h3>Sed ut perspiciatis unde omnis iste</h3><p>Nemo enim ipsam voluptatem quia voluptas sit aspernatur aut odit aut fugit, sed quia consequuntur.</p><a href="#" class="more">READ MORE</a></div>
  </article>
  <article class="card resource" style="left:795px">
    <div class="thumb" role="img" aria-label="Photo of a businessman holding a glowing security globe" style="background:linear-gradient(135deg,#1a2230,#2c4f7a 50%,#121820)"></div>
    <div class="meta"><span class="cat">EVENTS</span><h3>Sed ut perspiciatis unde omnis iste</h3><p>Nemo enim ipsam voluptatem quia voluptas sit aspernatur aut odit aut fugit, sed quia consequuntur.</p><a href="#" class="more">READ MORE</a></div>
  </article>
  <div class="dots"><span></span><span></span><span></span><span></span></div>
</section>

<section class="client-list">
  <h2 class="heading centered" style="top:3974px">OUR CLIENTS</h2>
  <div class="clients">
    <span class="client-name">Bri</span>
    <span class="client-name">Pindle</span>
    <span class="client-name">Tellix</span>
  </div>
</section>

<footer class="site-footer">
  <span class="footer-glow"></span>
  <div class="brand footer-brand">
    <span class="brand-mark"></span>
    <span class="brand-name">VORPLEXA</span>
  </div>
  <p class="footer-about">Sed ut perspiciatis unde omnis iste natus error sit&nbsp; voluptatem accusantium doloremque&nbsp; laudantium, totam rem aperiam.</p>
  <div class="footer-col" style="left:406px"><h5>COMPANY</h5><ul>
    <li>- About Us</li><li>- Why Vorplexa?</li><li>- Acreditations</li><li>- Quorvane Tellix Partner</li><li>- Net Promoter Score</li><li>- Careers</li><li>- Contact Us</li></ul></div>
  <div class="footer-col" style="left:660px"><h5>WHAT WE DO</h5><ul>
    <li>- Cloud Adoption</li><li>- Managed Services</li><li>- Optimise</li></ul></div>
  <div class="footer-col" style="left:912px"><h5>RESOURCES</h5><ul>
    <li>- News</li><li>- Resources</li><li>- Events</li><li>- Webinars</li><li>- Not for profit</li><li>- Case Studies</li></ul></div>
  <span class="footer-rule"></span>
  <p class="copyright">Copyright © 2021. Company Name. All Right Reserved</p>
  <div class="social" aria-label="Social links"><span></span><span></span><span></span><span></span><span></span></div>
</footer>

</body>
</html>
```